We need a new design/function for our reusable Sandwich paper bag

1. We need a designer who can help us create a design and improve the functionality of our paper lunch bag (image attached) and create "a new design for our new sandwich paper bag".

We would like to see designs for people age +18 ( working men, collage). The sandwich paper bag design should have a zipper (colored zipper is available) at the top, the sandwich bag dimension will be 8.5 x7.75x 1.5 in

2. The designer must also design a simple package cover for the sandwich bag

The feature of the material that will be used in manufacturing the sandwich paper bag: It combines the advantages of paper, film, and weaving. It is thinner than paper, but it is tough and tear resistant, texture and touch. Unique, waterproof, anti-fouling and weather-resistant, environmentally friendly and recyclable, has been widely used in textile

Target Market(s)

USA, Canada

Colors

Designer to choose colors to be used in the design.

Requirements
Must have
• Design for the sandwich paper bag
• Package design for the sandwich bag
• The designer must remember that there should be a zipper at the top of the bag
• Kindly find a suitable and small place to put our logo in it, besides the bag
Nice to have
• Try to design something that covers the crumpled paper bag look or appear it in a fashion way
• We appreciate if we can see an improvement in the functionality of the paper sandwich bag, not only the design. We need a new idea on how people will use this bag
Should not have
• Please don't use food images in your design

```html
<!DOCTYPE html>
<html lang="en">
<head>
<meta charset="utf-8">
<title>Eat. Travel. Repeat. – Sandwich Bag Face</title>
<link href="https://fonts.googleapis.com/css2?family=Fira+Sans:wght@400;800&display=swap" rel="stylesheet">
<style>
  :root {
    --kraft: #d2a77a;
    --kraft-light: #ddb88e;
    --signal-red: #ef5a58;
    --deep-red: #b63b3a;
    --chalk: #ece9e4;
    --zipper: #f4c21b;
    --zipper-dark: #e0a90f;
    --halftone: rgba(240, 232, 222, 0.55);
  }
  html, body {
    margin: 0;
    padding: 0;
    width: 1200px;
    height: 901px;
    overflow: hidden;
    background: var(--kraft);
  }
  .bag-face {
    display: block;
    width: 1200px;
    height: 901px;
  }
  .slogan {
    font-family: "Fira Sans", sans-serif;
    font-weight: 800;
    fill: var(--chalk);
  }
  .brand-tag-text {
    font-family: "Fira Sans", sans-serif;
    font-weight: 400;
    font-size: 17px;
    letter-spacing: 1px;
    fill: var(--chalk);
  }
</style>
</head>
<body>
<svg class="bag-face" viewBox="0 0 1200 901" xmlns="http://www.w3.org/2000/svg">
  <defs>
    <linearGradient id="kraft-fill" x1="0" y1="0" x2="1" y2="1">
      <stop offset="0" stop-color="var(--kraft-light)"/>
      <stop offset="1" stop-color="var(--kraft)"/>
    </linearGradient>
  </defs>

  <!-- kraft body -->
  <rect class="kraft-body" x="0" y="0" width="1200" height="901" fill="url(#kraft-fill)"/>

  <!-- zipper band -->
  <g class="zipper">
    <rect x="0" y="0" width="1200" height="47" fill="var(--zipper)"/>
    <rect x="0" y="38" width="1200" height="9" fill="var(--zipper-dark)"/>
  </g>

  <!-- red long-shadow block -->
  <polygon class="shadow-block"
    points="0,598 364,280 784,280 827,404 728,668 728,715 1200,715 1200,901 0,901"
    fill="var(--signal-red)"/>

  <!-- halftone areas -->
  <rect class="halftone-left" x="5" y="47" width="265" height="854" fill="var(--halftone)" opacity="0.45"
        role="img" aria-label="Halftone dot pattern fading down the left side"/>
  <rect class="halftone-right" x="884" y="342" width="316" height="373" fill="var(--halftone)" opacity="0.45"
        role="img" aria-label="Halftone dot pattern on the right side"/>

  <!-- slogan -->
  <text class="slogan" x="364" y="416" font-size="198" textLength="420" lengthAdjust="spacingAndGlyphs">EAT</text>
  <circle cx="808" cy="397" r="21" fill="var(--chalk)"/>
  <text class="slogan" x="368" y="500" font-size="86" textLength="402" lengthAdjust="spacingAndGlyphs">TRAVEL</text>
  <circle cx="803" cy="480" r="19" fill="var(--chalk)"/>
  <text class="slogan" x="378" y="579" font-size="86" textLength="392" lengthAdjust="spacingAndGlyphs">REPEAT</text>
  <circle cx="803" cy="566" r="19" fill="var(--chalk)"/>

  <!-- city-burger illustration area -->
  <rect class="city-illustration" x="402" y="590" width="283" height="265" rx="40"
        fill="var(--deep-red)" opacity="0.35"
        role="img" aria-label="Line illustration of a city skyline rising from a stacked bun"/>

  <!-- ground line -->
  <line class="ground-line" x1="666" y1="847" x2="1200" y2="847" stroke="var(--deep-red)" stroke-width="4"/>

  <!-- brand tag -->
  <g class="brand-tag">
    <rect x="1156" y="447" width="40" height="164" fill="var(--signal-red)" stroke="var(--chalk)" stroke-width="1.5"/>
    <text class="brand-tag-text" transform="translate(1183 600) rotate(-90)">COMPANY NAME</text>
  </g>
</svg>
</body>
</html>
```